Healthy Meal Delivery Website Needs to be updated, current, fresh and modern

Hi there,

The current website i have is super old and outdated.

I would like a beautiful modern site that has all the same content as the previous except with a a new, modern and trustworthy feel.

The current website is https://tovalplatefresh.com/

Target Market(s)

Health Conscious Young Professionals

Industry/Entity Type

Food Service

Font styles to use
Sans Serif

Requirements
Must have
• Modern Trustworthy feel
Should not have
• Anything out dated or cheesy or scammy

```html
<!DOCTYPE html>
<html lang="en">
<head>
<meta charset="utf-8">
<title>Toval Plate – Healthy Meal Delivery</title>
<link href="https://fonts.googleapis.com/css2?family=Poppins:ital,wght@0,400;0,500;0,600;0,700;1,400&display=swap" rel="stylesheet">
<style>
:root{
  --blue:#1a9ad6;
  --yellow:#e6e619;
  --ink:#1e1e1e;
  --text:#333;
  --grey-band:#eeeeee;
  --footer:#ebebeb;
  --white:#fff;
}
*{box-sizing:border-box;margin:0;padding:0}
html,body{width:1200px;height:3557px;overflow:hidden}
body{font-family:"Poppins",Arial,sans-serif;color:var(--text);background:var(--white);position:relative}
section,header,footer,nav,div,a,p,h1,h2,h3,h4,svg.divider,svg.arrows{position:absolute}
a{text-decoration:none;color:inherit}

/* top bar */
.topbar{left:0;top:0;width:1200px;height:38px;background:var(--blue);color:var(--white);font-size:11px}
.topbar .contact{left:161px;top:11px;display:flex;gap:36px}
.topbar .signup{left:893px;top:0;width:76px;height:38px;line-height:38px;text-align:center;font-weight:500}
.topbar .login{left:969px;top:0;width:72px;height:38px;line-height:38px;text-align:center;background:var(--yellow);color:var(--ink);font-weight:500}

/* nav */
.nav{left:0;top:38px;width:1200px;height:80px;background:var(--white)}
.brand{display:flex;align-items:center;gap:10px;font-weight:600;color:var(--blue);font-size:20px}
.brand .dot{position:static;width:22px;height:22px;border-radius:50%;background:var(--yellow)}
.nav .brand{left:161px;top:25px}
.nav .menu{left:568px;top:31px;display:flex;gap:31px;font-size:12.5px;color:var(--ink)}
.nav .menu a{position:static}

/* hero */
.hero{left:0;top:118px;width:1200px;height:466px;background:linear-gradient(90deg,#2b2b2b 0%,#3a3a38 35%,#5b8a34 60%,#8fae3f 80%,#c24a3a 100%)}
.hero h1{left:161px;top:138px;font-size:48px;line-height:62px;font-weight:700;color:var(--white);letter-spacing:-1px}
.hero h1 .hl{color:var(--yellow)}
.hero .dots{left:570px;top:420px;display:flex;gap:5px}
.hero .dots i{display:block;width:11px;height:11px;border-radius:50%;background:var(--white)}
.hero .dots i.on{background:var(--blue)}

/* shared headings */
.section-title{width:1200px;left:0;text-align:center;font-size:28px;font-weight:600;color:var(--ink)}
.section-title .accent{color:var(--blue)}
.divider{left:490px;width:220px;height:24px}

/* programs */
.programs{left:0;top:584px;width:1200px;height:571px;background:var(--white)}
.card{top:175px;width:273px}
.card .photo{position:relative;width:273px;height:161px}
.card h3{position:relative;margin-top:16px;font-size:18px;font-weight:500;color:var(--ink)}
.card p{position:relative;margin-top:8px;font-size:10.5px;line-height:21px;color:#444}
.btn-yellow{background:var(--yellow);color:var(--ink);font-size:11px;font-weight:600;text-transform:uppercase;display:inline-block}
.card .btn-yellow{position:relative;margin-top:12px;width:90px;height:32px;line-height:32px;text-align:center}

/* delivery */
.delivery{left:0;top:1155px;width:1200px;height:645px;background:var(--yellow)}
.delivery h2{left:0;top:78px;width:1200px;text-align:center;font-size:27px;line-height:40px;font-weight:600;color:var(--ink)}
.delivery h2 .accent{color:var(--blue)}
.feature{left:161px;width:420px;height:90px}
.feature svg{position:absolute;left:0;top:0}
.feature h4{left:84px;top:0;font-size:16px;font-weight:600;color:var(--blue)}
.feature p{left:84px;top:34px;width:335px;font-size:10px;line-height:22px;color:var(--ink)}

/* menu */
.menu-items{left:0;top:1800px;width:1200px;height:710px;background:var(--white)}
.tabs{left:381px;top:185px;display:flex;gap:12px;font-size:12px;font-weight:600;color:var(--blue)}
.tabs span{padding:5px 16px}
.tabs .active{background:var(--yellow);color:var(--ink)}
.tile{width:211px;height:173px}
.more{left:576px;top:624px;width:46px;height:20px;border:1.5px solid var(--ink);border-radius:10px;display:flex;justify-content:center;align-items:center;gap:3px}
.more i{width:4px;height:4px;background:var(--ink);border-radius:50%;display:block}

/* testimonials */
.testimonials{left:0;top:2510px;width:1200px;height:483px;background:var(--grey-band)}
.avatar{left:161px;top:225px;width:131px;height:131px;border-radius:50%;background:linear-gradient(135deg,#d9c2b0,#8a6a55)}
.quote{left:320px;top:222px;width:470px;font-size:11.5px;line-height:25px;font-style:italic;color:#444}
.reviewer{left:320px;top:336px;font-size:13px;font-weight:600;color:var(--blue)}
.arrows{left:604px;top:405px;width:110px;height:20px}
.plate{left:783px;top:206px;width:417px;height:277px;border-radius:210px 0 0 210px;background:radial-gradient(circle at 45% 50%,#e4d2b8 0 30%,#6c9b3a 45%,#4a3a2c 70%,#8a7a6a 100%)}

/* cta */
.cta{left:0;top:2993px;width:1200px;height:287px;background:var(--white)}
.cta h2{left:0;top:88px;width:1200px;text-align:center;font-size:27px;line-height:40px;font-weight:600;color:var(--ink)}
.cta h2 .accent{color:var(--blue)}
.cta .btn{top:185px;height:30px;line-height:30px;text-align:center;font-size:12px}
.cta .login-btn{left:474px;width:124px;background:var(--blue);color:var(--white)}
.cta .signup-btn{left:605px;width:118px;background:var(--yellow);color:var(--ink)}

/* footer */
.footer{left:0;top:3280px;width:1200px;height:277px;background:var(--footer);color:var(--ink)}
.footer h4{top:46px;font-size:14px;font-weight:500}
.footer .col{top:80px;font-size:11px;line-height:24px}
.footer .social{left:892px;top:82px;display:flex;gap:14px;align-items:center}
.footer .brand{left:161px;top:232px;font-size:20px}
.footer .legal{left:702px;top:238px;font-size:11px}
.footer .code{left:1071px;top:238px;font-size:11px}
</style>
</head>
<body>

<header class="topbar">
  <div class="contact"><span>&#9742; Phone: 416-555-0142</span><span>&#9993; Email: hello@tovalplatefresh.com</span></div>
  <a class="signup" href="#">SIGN UP</a>
  <a class="login" href="#">LOGIN</a>
</header>

<nav class="nav">
  <div class="brand"><span class="dot"></span>Toval Plate</div>
  <div class="menu"><a>Home</a><a>Toval Meal Plans</a><a>Menu</a><a>Pricing</a><a>About</a><a>Press</a><a>Contact</a></div>
</nav>

<section class="hero" role="img" aria-label="Fresh salad of spinach, tomato, cucumber and onion beside a bowl of grains on dark slate">
  <h1><span class="hl">Fresh</span> and<br>so Delicious</h1>
  <div class="dots"><i class="on"></i><i></i><i></i><i></i></div>
</section>

<section class="programs">
  <h2 class="section-title" style="top:78px">Three Toval <span class="accent">Diet Programs</span></h2>
  <svg class="divider" style="top:122px" viewBox="0 0 220 24"><line x1="0" y1="12" x2="98" y2="12" stroke="#1a9ad6"/><line x1="122" y1="12" x2="220" y2="12" stroke="#1a9ad6"/><circle cx="110" cy="12" r="11" fill="#e6e619"/></svg>

  <div class="card" style="left:161px">
    <div class="photo" role="img" aria-label="Oatmeal bowl topped with berries" style="background:linear-gradient(135deg,#2a2326,#d9cfc3 50%,#6a2236)"></div>
    <h3>Toval Diet</h3>
    <p>Sed ut perspiciatis unde omnis iste natus er ror sit voluptatem accusantium dolore mque laudantium, totam rem aperiam.</p>
    <a class="btn-yellow">Read more</a>
  </div>
  <div class="card" style="left:463px">
    <div class="photo" role="img" aria-label="Green salad with tomatoes and feta" style="background:linear-gradient(135deg,#3c6a22,#7fb23e 50%,#c43a2a)"></div>
    <h3>Toval Veggie</h3>
    <p>Sed ut perspiciatis unde omnis iste natus er ror sit voluptatem accusantium dolore mque laudantium, totam rem aperiam.</p>
    <a class="btn-yellow">Read more</a>
  </div>
  <div class="card" style="left:765px">
    <div class="photo" role="img" aria-label="Salad with sliced chicken and radish" style="background:linear-gradient(135deg,#c9a890,#7aa84a 50%,#d46a4a)"></div>
    <h3>A La Carte</h3>
    <p>Sed ut perspiciatis unde omnis iste natus er ror sit voluptatem accusantium dolore mque laudantium, totam rem aperiam.</p>
    <a class="btn-yellow">Read more</a>
  </div>
  <div role="img" aria-label="Spinach leaves" style="left:0;top:430px;width:110px;height:141px;background:radial-gradient(ellipse at 30% 70%,#4d9a2e,#2f6a1c 70%,transparent 71%)"></div>
</section>

<section class="delivery">
  <h2>The Toval Diet delivers diet meals to<br>your door in <span class="accent">Toronto, GTA</span> and Montreal</h2>
  <svg class="divider" style="top:168px" viewBox="0 0 220 24"><line x1="0" y1="12" x2="98" y2="12" stroke="#1a9ad6"/><line x1="122" y1="12" x2="220" y2="12" stroke="#1a9ad6"/><circle cx="110" cy="12" r="11" fill="#1a9ad6"/></svg>

  <div class="feature" style="top:245px">
    <svg width="60" height="60" viewBox="0 0 60 60"><path d="M30 54 C10 38 4 28 4 19 A13 13 0 0 1 30 13 A13 13 0 0 1 56 19 C56 28 50 38 30 54Z" fill="#1a9ad6"/><path d="M30 20v18M21 29h18" stroke="#e6e619" stroke-width="5"/></svg>
    <h4>Healthy</h4>
    <p>The Toval Diet is a great way to ensure you are eating all the nutrients you need, and nothing your body doesn't need.</p>
  </div>
  <div class="feature" style="top:346px">
    <svg width="60" height="60" viewBox="0 0 60 60"><circle cx="30" cy="30" r="15" fill="none" stroke="#1a9ad6" stroke-width="4"/><path d="M8 10v40M4 10v12h8V10M52 10c-5 4-5 16 0 20v20" fill="none" stroke="#1a9ad6" stroke-width="3"/></svg>
    <h4>Choice</h4>
    <p>The Toval Diet is a great way to ensure you are eating all the nutrients you need, and nothing your body doesn't need.</p>
  </div>
  <div class="feature" style="top:456px">
    <svg width="60" height="60" viewBox="0 0 60 60"><path d="M8 52 C8 22 26 8 54 6 C52 34 38 50 8 52Z" fill="#1a9ad6"/><path d="M8 52 L40 20" stroke="#e6e619" stroke-width="3"/></svg>
    <h4>Fresh</h4>
    <p>The Toval Diet is a great way to ensure you are eating all the nutrients you need, and nothing your body doesn't need.</p>
  </div>

  <div role="img" aria-label="Glass bowl of guacamole with tortilla chips and basil" style="left:652px;top:245px;width:384px;height:343px;border-radius:50%;background:radial-gradient(circle,#a8c25a 0 45%,#6f9b3a 62%,#d9e6c8 72%,transparent 73%)"></div>
  <div role="img" aria-label="Tortilla chips topped with guacamole" style="left:1040px;top:220px;width:160px;height:340px;background:linear-gradient(160deg,transparent 10%,#d49a3a 30%,#a6c04e 55%,#d49a3a 80%,transparent 95%)"></div>
  <div role="img" aria-label="Tortilla chip with guacamole" style="left:965px;top:0;width:140px;height:100px;background:radial-gradient(ellipse at 50% 30%,#b8c652,#d39a3c 60%,transparent 62%)"></div>
</section>

<section class="menu-items">
  <h2 class="section-title" style="top:78px">Select From Over <span class="accent">100 Menu</span> Items</h2>
  <svg class="divider" style="top:122px" viewBox="0 0 220 24"><line x1="0" y1="12" x2="98" y2="12" stroke="#1a9ad6"/><line x1="122" y1="12" x2="220" y2="12" stroke="#1a9ad6"/><circle cx="110" cy="12" r="11" fill="#e6e619"/></svg>
  <div class="tabs"><span class="active">ALL</span><span>SNACK</span><span>BREAKFAST</span><span>LUNCH</span><span>DINNER</span></div>

  <div class="tile" role="img" aria-label="Grilled steak with herbs" style="left:161px;top:235px;background:linear-gradient(135deg,#5a2a1a,#9a5a3a)"></div>
  <div class="tile" role="img" aria-label="Mixed salad in a bowl" style="left:382px;top:235px;background:linear-gradient(135deg,#e8ddd0,#8aa84a 55%,#c44a3a)"></div>
  <div class="tile" role="img" aria-label="Grilled kebab skewers" style="left:604px;top:235px;background:linear-gradient(135deg,#b07a4a,#d6a872)"></div>
  <div class="tile" role="img" aria-label="Bowl of guacamole dip" style="left:825px;top:235px;background:radial-gradient(circle,#b6c86a 35%,#3a5a2a 70%)"></div>
  <div class="tile" role="img" aria-label="Grilled chicken with peppers" style="left:161px;top:418px;background:linear-gradient(135deg,#e7c33a,#c84a2a 50%,#5a8a3a)"></div>
  <div class="tile" role="img" aria-label="Braised shrimp in a pan" style="left:382px;top:418px;background:linear-gradient(135deg,#2a1a14,#b8502a)"></div>
  <div class="tile" role="img" aria-label="Lemonade with lemon slices" style="left:604px;top:418px;background:linear-gradient(135deg,#8ab6d8,#f0e6a0 60%,#e8c43a)"></div>
  <div class="tile" role="img" aria-label="Roasted potatoes with meat" style="left:825px;top:418px;background:linear-gradient(135deg,#3a2a22,#c08a4a)"></div>
  <div class="more"><i></i><i></i><i></i></div>
  <div role="img" aria-label="Spinach leaves" style="left:1010px;top:570px;width:190px;height:140px;background:radial-gradient(ellipse at 60% 60%,#5aa83a,#2f6a1c 65%,transparent 66%)"></div>
</section>

<section class="testimonials">
  <h2 class="section-title" style="top:78px">What They <span class="accent">Say</span></h2>
  <svg class="divider" style="top:122px" viewBox="0 0 220 24"><line x1="0" y1="12" x2="98" y2="12" stroke="#1a9ad6"/><line x1="122" y1="12" x2="220" y2="12" stroke="#1a9ad6"/><circle cx="110" cy="12" r="11" fill="#e6e619"/></svg>
  <div class="avatar" role="img" aria-label="Portrait of a customer"></div>
  <p class="quote">Lorem ipsum dolor sit amet, consectetur adipiscing elit, sed do eiusmod tempor incididunt ut labore dolore magna aliqua. Ut enim ad minim veniam,Lorem ipsum dolor sit amet, consectetur adipiscing elied do eiusmod tempor incididunt ut labore et dolore magna aliqua.</p>
  <p class="reviewer">Mara Ellis, City Name</p>
  <svg class="arrows" viewBox="0 0 110 20"><path d="M40 10H2M10 3L2 10l8 7" fill="none" stroke="#1e1e1e" stroke-width="2"/><path d="M70 10h38M100 3l8 7-8 7" fill="none" stroke="#1e1e1e" stroke-width="2"/></svg>
  <div class="plate" role="img" aria-label="Plate of sliced grilled chicken over green salad"></div>
</section>

<section class="cta">
  <h2>The Toval DIET is based on real foods made<br>with fresh and <span class="accent">natural ingredients.</span></h2>
  <a class="btn login-btn">Customer Login</a>
  <a class="btn signup-btn">Sign Up Now</a>
</section>

<footer class="footer">
  <h4 style="left:161px">What Is Toval?</h4>
  <p class="col" style="left:161px;width:250px">Toval is the Toronto &amp; Montreal Diet Delivery program based on the Toval Diet&trade;, healthy carbs and the right fats.</p>
  <h4 style="left:465px">Links</h4>
  <p class="col" style="left:465px">Sed uetsdem<br>Comsisteat<br>Sed uerspici<br>Blog</p>
  <h4 style="left:624px">Stay In Touch</h4>
  <p class="col" style="left:624px">Toronto: 416-555-0142<br>Email: hello@tovalplatefresh.com</p>
  <h4 style="left:892px">Connect</h4>
  <div class="social">
    <svg width="24" height="18" viewBox="0 0 24 18"><rect x="1" y="1" width="22" height="16" fill="#1e1e1e"/><path d="M1 1l11 9 11-9" fill="none" stroke="#ebebeb" stroke-width="2"/></svg>
    <svg width="20" height="20" viewBox="0 0 20 20"><circle cx="10" cy="10" r="9" fill="#1e1e1e"/></svg>
    <svg width="20" height="20" viewBox="0 0 20 20"><circle cx="10" cy="10" r="9" fill="#1e1e1e"/></svg>
    <svg width="20" height="20" viewBox="0 0 20 20"><circle cx="10" cy="10" r="9" fill="#1e1e1e"/></svg>
  </div>
  <div class="brand"><span class="dot"></span>Toval Plate</div>
  <p class="legal">&copy; 2018 All Rights are Reserved. &nbsp;Privacy Policy | Terms of Use</p>
  <p class="code">C4</p>
</footer>

</body>
</html>
```